Detail Shop Business card design

i need a business card design for my new detailing company called 'Brisk's Polish Works'. i want an all black and white design . simple, direct and to the point. i want the designer to choose a fitting font to match the logothe front should have logo, address, phone and email and the back side should have a slogan and text indicating that we offer services on anything including cars, trucks, motorcycles and RVs. slogan will read "we take pride in your ride"
maybe also very small on the back side the IG icon with Brisks_Polish_Works

phone 208.417.6352
address 3847 E Larkin Ave
Spokane WA 99214
email: BrisksPolish@mailvexo.com

Target Market(s)

all ages , auto enthusiasts

Industry/Entity Type

Automotive

Contact Information for Business Card

the front should have logo, address, phone and email and the back side should have a slogan and text indicating that we offer services on anything including cars, trucks, motorcycles and RVs. slogan will read "we take pride in your ride"

phone 208.417.6352
address 3847 E Larkin Ave
Spokane WA 99214

Colors
000000
ffffff

Requirements
Must have
• bold font and very simple design with good spacing
Nice to have
• anything creative from the designer indicating we service any types of vehicles
Should not have
• any colors ,

```html
<!DOCTYPE html>
<html lang="en">
<head>
<meta charset="utf-8">
<title>Brisk's Polish Works – Business Card</title>
<link href="https://fonts.googleapis.com/css2?family=Lato:wght@300;400;900&display=swap" rel="stylesheet">
<style>
  :root {
    --ink: #000000;
    --paper: #ffffff;
    --backdrop: #e4e4e4;
  }
  * { margin: 0; padding: 0; box-sizing: border-box; }
  html, body {
    width: 1200px;
    height: 800px;
    overflow: hidden;
    background: var(--backdrop);
    font-family: "Lato", sans-serif;
  }
  .canvas {
    position: relative;
    width: 1200px;
    height: 800px;
  }
  .card {
    position: absolute;
    width: 525px;
    height: 300px;
    box-shadow: 0 10px 24px rgba(0,0,0,0.18);
  }
  .card-front {
    left: 70px;
    top: 400px;
    background: var(--paper);
    color: var(--ink);
  }
  .card-back {
    left: 605px;
    top: 100px;
    background: var(--ink);
    color: var(--paper);
  }
  .card-frame {
    position: absolute;
    inset: 14px;
    border: 2px solid currentColor;
    display: flex;
    flex-direction: column;
    align-items: center;
    justify-content: center;
  }
  .brand-mark {
    display: flex;
    align-items: center;
    gap: 10px;
  }
  .brand-dot {
    width: 14px;
    height: 14px;
    border-radius: 50%;
    background: currentColor;
  }
  .brand-name {
    font-weight: 900;
    font-size: 30px;
    letter-spacing: 1px;
    text-transform: uppercase;
    line-height: 1;
  }
  .contact {
    margin-top: 26px;
    text-align: center;
    font-weight: 400;
    font-size: 15px;
    line-height: 1.5;
  }
  .contact b { font-weight: 900; }
  .slogan {
    margin-top: 24px;
    font-weight: 300;
    font-size: 15px;
    letter-spacing: 5px;
  }
</style>
</head>
<body>
  <main class="canvas">
    <section class="card card-back" aria-label="Card back">
      <div class="card-frame">
        <div class="brand-mark">
          <span class="brand-dot"></span>
          <span class="brand-name">Brisk's Polish Works</span>
        </div>
        <p class="slogan">we take pride in your ride</p>
      </div>
    </section>

    <section class="card card-front" aria-label="Card front">
      <div class="card-frame">
        <div class="brand-mark">
          <span class="brand-dot"></span>
          <span class="brand-name">Brisk's Polish Works</span>
        </div>
        <p class="contact">
          <b>P:</b> 208.417.6352 | <b>E:</b> BrisksPolish@mailvexo.com<br>
          3847 E Larkin Ave, Spokane WA 99214
        </p>
      </div>
    </section>
  </main>
</body>
</html>
```